Brightwater Care Partners, LLC Business Card update!

would like a classier business card. Our cards currently just have our logo and contact information. Need better use of color and creativity
Logo attached.

Target Market(s)

Potential clients, contacts, existing clients. We are a consulting company

Industry/Entity Type

Business

Contact Information for Business Card

We like our colors but just have a boring card with our logo and a white background. I want something that stands out.

Colors
ec1f27
757575

Requirements
Must have
• Color to stay consistent. Logo provided
Nice to have
• Just better use of color/ design

```html
<!DOCTYPE html>
<html lang="en">
<head>
<meta charset="utf-8">
<title>Brightwater Care Partners – Business Card</title>
<link rel="stylesheet" href="https://fonts.googleapis.com/css2?family=Open+Sans:ital,wght@0,400;0,600;0,700;1,400&display=swap">
<style>
  :root {
    --brand-red: #ec1f27;
    --brand-grey: #757575;
    --card-white: #ffffff;
    --stage: #2a2a2a;
    --text-on-red: #ffffff;
  }
  * { box-sizing: border-box; margin: 0; padding: 0; }
  html, body {
    width: 1200px;
    height: 900px;
    overflow: hidden;
    background: var(--stage);
    font-family: "Open Sans", Arial, sans-serif;
  }
  .canvas {
    position: relative;
    width: 1200px;
    height: 900px;
  }
  .business-card {
    position: absolute;
    left: 180px;
    top: 210px;
    width: 840px;
    height: 480px;
    background: var(--card-white);
    overflow: hidden;
  }
  .card-header {
    position: absolute;
    inset: 0 0 auto 0;
    height: 205px;
    display: flex;
    align-items: center;
    justify-content: center;
    gap: 22px;
  }
  .brand-dot {
    width: 64px;
    height: 64px;
    border-radius: 50%;
    background: var(--brand-grey);
    flex: none;
  }
  .brand-name {
    color: var(--brand-red);
    font-weight: 400;
    font-size: 46px;
    letter-spacing: 0.5px;
    line-height: 1;
  }
  .card-band {
    position: absolute;
    left: 0;
    right: 0;
    bottom: 0;
    height: 275px;
    background: var(--brand-red);
    color: var(--text-on-red);
  }
  .owner {
    position: absolute;
    left: 150px;
    top: 62px;
  }
  .owner-name {
    font-weight: 700;
    font-size: 23px;
    line-height: 1.2;
  }
  .owner-role {
    font-style: italic;
    font-size: 18px;
    line-height: 1.3;
  }
  .contact-list {
    position: absolute;
    left: 385px;
    top: 30px;
    list-style: none;
  }
  .contact-item {
    display: flex;
    align-items: center;
    gap: 12px;
    height: 34px;
    font-size: 18px;
  }
  .contact-icon {
    width: 24px;
    height: 24px;
    border-radius: 5px;
    background: var(--card-white);
    display: flex;
    align-items: center;
    justify-content: center;
    flex: none;
  }
  .contact-icon svg {
    width: 15px;
    height: 15px;
    fill: var(--brand-red);
    stroke: var(--brand-red);
  }
</style>
</head>
<body>
<main class="canvas">
  <section class="business-card" aria-label="Business card">
    <header class="card-header">
      <span class="brand-dot" aria-hidden="true"></span>
      <span class="brand-name">Brightwater Care Partners</span>
    </header>

    <div class="card-band">
      <div class="owner">
        <p class="owner-name">Owner Name</p>
        <p class="owner-role">Managing Director</p>
      </div>

      <ul class="contact-list">
        <li class="contact-item">
          <span class="contact-icon" aria-hidden="true">
            <svg viewBox="0 0 16 16"><path stroke="none" d="M3 2h3l1 3-2 1.2a8 8 0 0 0 4.8 4.8L11 9l3 1v3a1 1 0 0 1-1 1A12 12 0 0 1 2 3a1 1 0 0 1 1-1z"/></svg>
          </span>
          <span>000 123 456 456</span>
        </li>
        <li class="contact-item">
          <span class="contact-icon" aria-hidden="true">
            <svg viewBox="0 0 16 16"><rect x="2" y="4" width="12" height="8" rx="1" stroke="none"/><path d="M2.5 4.5 8 9l5.5-4.5" fill="none" stroke="#fff" stroke-width="1.2"/></svg>
          </span>
          <span>iinfo@compnayname.com</span>
        </li>
        <li class="contact-item">
          <span class="contact-icon" aria-hidden="true">
            <svg viewBox="0 0 16 16"><path d="M7 9.5 9.5 7M6.5 6 5 7.5a2.1 2.1 0 0 0 3 3l1.5-1.5M9.5 10 11 8.5a2.1 2.1 0 0 0-3-3L6.5 7" fill="none" stroke-width="1.6" stroke-linecap="round"/></svg>
          </span>
          <span>www.companyname.com</span>
        </li>
        <li class="contact-item">
          <span class="contact-icon" aria-hidden="true">
            <svg viewBox="0 0 16 16"><path stroke="none" d="M8 1.5a4.5 4.5 0 0 0-4.5 4.5C3.5 9.5 8 14.5 8 14.5S12.5 9.5 12.5 6A4.5 4.5 0 0 0 8 1.5zm0 6.3a1.8 1.8 0 1 1 0-3.6 1.8 1.8 0 0 1 0 3.6z"/></svg>
          </span>
          <span>Address line1, Address Line, country, 012</span>
        </li>
      </ul>
    </div>
  </section>
</main>
</body>
</html>
```